Silver Lanterns - Media Kit & Rate Card Package for Advertisers

Hi,
I write a lifestyle blog which centres around food, wine and travel. I send my media kit out to potential sponsors, PR companies and product representatives.

I need to make my media kit look gorgeous!
In the kit I would like to have active links to past stories and active social media buttons in the electronic copy.

I don't like how the images are distinct from the text and think perhaps an overlay may look ok with text over a more transparent image.

I like my logo and don't want that to change. I want the kit to look attractive, sophisticated and well branded to silver lanterns.

I would also like to be able to take the media kit to the printers and have a nice glossy kit printed to hand local advertisers.

I have tried to include all the relevant information in the existing kit so a graphic designer can just put the necessary texts, tables and rate cards into and attractive and co-hesive document. I have included a selection of images which suit my website. Feel free to use as many or as few as you think the document requires. If you feel you would like to add a stock image than be my guest. I am interested it seeing a range of designs.

I am only a small blog and am only just breaking even at the moment. I am really hope this media kit makes me look more professional and impressive and enables me to attract a sponsored partnership.

I don't know what the going rate is for this kind of work so if my budget is too lean could you please tell me rather than ignore the job request.

Target Market(s)

Brand Sponsors, Airline Sponsors, PR Agencies, Advertising Purchasers, Tourism Agencies & Departments, Premium Hotel Chains, Package Holiday Specialists, Wellness Retreats, Cruise Lines

Industry/Entity Type

Travel

Font styles to use
Serif

Requirements
Must have
• I need to make my media kit look gorgeous!
• In the electronic copy I would like to have active links to past stories and active social.
• Must include all the tables, text and a rate card.
• Needs Social Media Buttons.
• Needs to use my logo and follow my branding. (I included my logo and a copy of my business card)
Nice to have
• I want it to look, elegant, sophisticated and modern. I want it to have equal focus visually on food, wine and travel.
Should not have
• I don't want it to look boxes or squashed.

```html
<!DOCTYPE html>
<html lang="en">
<head>
<meta charset="utf-8">
<title>Silver Lanterns Media Kit</title>
<link rel="stylesheet" href="https://fonts.googleapis.com/css2?family=Oswald:wght@300&family=Open+Sans:wght@400;600&display=swap">
<style>
  :root {
    --plum: #8a4a9c;
    --plum-soft: #c9a6d3;
    --ink: #2b2b2b;
    --body: #555555;
    --paper: #ffffff;
  }
  * { box-sizing: border-box; margin: 0; padding: 0; }
  html, body { width: 900px; height: 1200px; overflow: hidden; background: var(--paper); }
  .kit { position: relative; width: 900px; height: 1200px; font-family: "Open Sans", sans-serif; color: var(--body); }

  .brand { position: absolute; left: 30px; top: 62px; }
  .brand-name { font-family: "Open Sans", sans-serif; font-weight: 600; font-size: 42px; line-height: 1; color: var(--ink); }

  .flourish { position: absolute; left: 390px; top: 10px; width: 230px; height: 160px;
    background: radial-gradient(ellipse at 40% 50%, var(--plum-soft) 0%, rgba(201,166,211,0.25) 55%, rgba(255,255,255,0) 75%); }

  .social { position: absolute; top: 51px; left: 627px; display: flex; gap: 12px; }
  .social a { display: block; width: 54px; height: 54px; border-radius: 50%; background: var(--plum); }

  .kit-label { position: absolute; left: 672px; top: 118px; font-family: "Oswald", sans-serif; font-weight: 300;
    font-size: 66px; line-height: 1; color: var(--plum); }

  .rate-card { position: absolute; left: 30px; right: 30px; top: 228px; }
  .rate-title { font-family: "Oswald", sans-serif; font-weight: 300; font-size: 46px; line-height: 1.1; color: var(--plum); margin-bottom: 10px; }
  .offer { margin-bottom: 23px; }
  .offer h2 { font-size: 26px; font-weight: 600; color: var(--ink); line-height: 36px; }
  .offer p { font-size: 15.5px; line-height: 28px; }
  .offer .price { display: inline-block; font-size: 15.5px; line-height: 28px; color: var(--plum); text-decoration: none; }
</style>
</head>
<body>
<main class="kit">
  <header>
    <div class="brand">
      <p class="brand-name">Silver Lanterns</p>
    </div>
    <div class="flourish" role="img" aria-label="Decorative flourish in soft plum and grey"></div>
    <nav class="social" aria-label="Social media">
      <a href="#" aria-label="Social profile one"></a>
      <a href="#" aria-label="Social profile two"></a>
      <a href="#" aria-label="Social profile three"></a>
      <a href="#" aria-label="Social profile four"></a>
    </nav>
    <h1 class="kit-label">Media Kit</h1>
  </header>

  <section class="rate-card">
    <h2 class="rate-title">Silver Lanterns' Rate Card</h2>

    <article class="offer">
      <h2>Recipe Sponsorships</h2>
      <p>Silver Lanterns produces a stunning recipe each week. These recipes continue to perform well long after they are published. Typically they get listed on sites such as Platewatch, Tastefinder, Dine Daily, Fresh Frame &amp; Pinboard Collaborative boards with more than 14 million followers. Sponsoring a recipe means I can get your product seen by more people than just my direct audience!</p>
      <a class="price" href="#">Sponsor today from $120 + Product</a>
    </article>

    <article class="offer">
      <h2>Getaway Sponsorships</h2>
      <p>Silver Lanterns writes articles which cover area reviews, accommodation reviews, romantic getaway ideas, cooking schools and foodie escapes. If your business would like assistance promoting your product please feel free to contact me for detailed information.</p>
      <a class="price" href="#">Sponsored stories start from $160 + Product</a>
    </article>

    <article class="offer">
      <h2>Social Media Publicity Shout Outs</h2>
      <p>Do you have something to say? Let me help you create some hype! I will create an engaging pin or a great photoline image from your artwork and shout it out to my following. This is a great way to raise brand awareness.</p>
      <a class="price" href="#">Social Media Shout outs from $100</a>
    </article>

    <article class="offer">
      <h2>Side Bar Advertising - 2 Spots Only</h2>
      <p>Have your advertisement appear above the fold in our sidebar. The advertisement will appear on all Silver Lanterns pages and can include an image, 200px X 400px, text and clickable link. Your ad will rotate to ensure maximum visibility to all sponsors.</p>
      <a class="price" href="#">Advertising $100 per 2 weeks</a>
    </article>

    <article class="offer">
      <h2>Competition Advertising</h2>
      <p>Competitions are a great way to create excitement! A giveaway heightens brand and product awareness. Through enticements which encourage viral sharing on photoline, chirper or Circlebook we can create product buzz! We design campaigns that brings entrants to your site and help create a mailing list for future campaigns.</p>
      <a class="price" href="#">Competition $160 + Product + Mailing to Winner</a>
    </article>
  </section>
</main>
</body>
</html>
```